Velvette by Marisa Dunn business cards

I am after a business card that will fit the name of my business - velvette.
I want something classy and sexy and nothing tacky.
Ideas that I like are Zebra print backgrounds glitter back grounds
Two ideas I had were
1. Zebra print in black and white, the name Velvette by Marisa Dunn and a shilouette of a woman laying on top of the name. Or instead of zebra a glitter background.
2. Idea very similar except for instead of a woman a pair of lips maybe a hot pink glitter or a gold glitter depending on background with the business name between the lips.
Or you can do something completely different.

```html
<!DOCTYPE html>
<html lang="en">
<head>
<meta charset="utf-8">
<title>Velvette by Marisa Dunn – Business Card</title>
<link rel="stylesheet" href="https://fonts.googleapis.com/css2?family=Poppins:wght@300;600&display=swap">
<style>
  :root {
    --ink: #231f20;
    --ink-soft: #4a4646;
    --paper-light: #ffffff;
    --paper-mid: #e4e4e4;
    --paper-edge: #c4c4c4;
    --stripe-light: #dcdcdc;
  }
  html, body {
    margin: 0;
    padding: 0;
    overflow: hidden;
    background: var(--paper-edge);
  }
  .card {
    position: relative;
    width: 686px;
    height: 1200px;
    overflow: hidden;
    background: radial-gradient(ellipse 75% 55% at 52% 46%, var(--paper-light) 0%, var(--paper-mid) 45%, var(--paper-edge) 100%);
    font-family: "Poppins", "Century Gothic", sans-serif;
    color: var(--ink-soft);
  }
  .identity {
    position: absolute;
    left: 36px;
    top: 143px;
    line-height: 1;
  }
  .identity__name {
    margin: 0;
    font-weight: 600;
    font-size: 58px;
    color: var(--ink);
    letter-spacing: 0.5px;
  }
  .identity__role {
    margin: 2px 0 0;
    font-weight: 300;
    font-size: 50px;
    color: var(--ink-soft);
  }
  .identity-rule {
    position: absolute;
    left: 0;
    top: 261px;
    width: 617px;
    height: 8px;
    background: linear-gradient(90deg, var(--ink-soft) 0%, var(--ink-soft) 45%, rgba(74,70,70,0) 100%);
  }
  .contact {
    position: absolute;
    right: 11px;
    top: 0;
    width: 660px;
    margin: 0;
    font-style: normal;
    font-weight: 300;
    font-size: 43px;
    line-height: 1;
    text-align: right;
    color: var(--ink-soft);
  }
  .contact__line {
    position: absolute;
    right: 0;
    white-space: nowrap;
  }
  .contact__street { top: 452px; }
  .contact__city   { top: 515px; }
  .contact__phone  { top: 623px; }
  .contact__mobile { top: 715px; }
  .contact__email  { top: 806px; }
  .band-rule {
    position: absolute;
    left: 90px;
    right: 0;
    top: 895px;
    height: 7px;
    background: linear-gradient(90deg, rgba(74,70,70,0) 0%, var(--ink-soft) 35%, var(--ink-soft) 100%);
  }
  .stripe-band {
    position: absolute;
    left: 0;
    right: 0;
    top: 903px;
    bottom: 0;
    background: linear-gradient(160deg, var(--ink-soft) 0%, #7d7a7a 35%, var(--stripe-light) 55%, #6a6767 80%, var(--ink-soft) 100%);
  }
</style>
</head>
<body>
  <div class="card" aria-label="Velvette by Marisa Dunn business card">
    <header class="identity">
      <h1 class="identity__name">Marisa Dunn</h1>
      <p class="identity__role">Proprietor</p>
    </header>
    <div class="identity-rule"></div>

    <address class="contact">
      <span class="contact__line contact__street">18, Marlowe Crescent</span>
      <span class="contact__line contact__city">Westbrook, CA 90417</span>
      <span class="contact__line contact__phone">555310482</span>
      <span class="contact__line contact__mobile">555720946</span>
      <span class="contact__line contact__email">hello@velvettebymd.com</span>
    </address>

    <div class="band-rule"></div>
    <div class="stripe-band" role="img" aria-label="Zebra print pattern in charcoal and light grey stripes"></div>
  </div>
</body>
</html>
```